Harborline Auto LLC

Car Dealer Customer Service
Address: 2874 Cresthaven Road, Shelbyville, TN 37162
web: www.harborlineautoxq.net
email: harborlineautoxq@mailnest.example
Phone: (931) 555-0148
Phone: (629) 555-0173

```html
<!DOCTYPE html>
<html lang="en">
<head>
<meta charset="utf-8">
<title>Harborline Auto – Business Card</title>
<link href="https://fonts.googleapis.com/css2?family=Poppins:wght@400;600;700&display=swap" rel="stylesheet">
<style>
  :root {
    --bg: #2b2b2d;
    --card: #1f1f22;
    --card-edge: #2a2a2e;
    --blue: #2a8ccc;
    --blue-deep: #15587f;
    --gold: #e0a93a;
    --text: #f2f2f2;
    --muted-mark: #141416;
  }
  * { margin: 0; padding: 0; box-sizing: border-box; }
  html, body { width: 1200px; height: 1138px; overflow: hidden; }
  body {
    background: var(--bg);
    font-family: "Poppins", sans-serif;
    color: var(--text);
    position: relative;
  }
  .card {
    position: absolute;
    border-radius: 16px;
    background: linear-gradient(160deg, var(--card-edge), var(--card));
    overflow: hidden;
  }
  .card-front { left: 274px; top: 186px; width: 622px; height: 374px; }
  .card-back  { left: 276px; top: 608px; width: 618px; height: 374px; }

  .front-name {
    position: absolute; left: 0; right: 0; top: 150px;
    text-align: center; font-weight: 700; font-size: 46px;
    color: var(--muted-mark); letter-spacing: 1px;
  }
  .front-web {
    position: absolute; left: 0; right: 0; top: 333px;
    display: flex; justify-content: center; align-items: center; gap: 22px;
    font-size: 15px;
  }
  .front-web .rule { width: 54px; height: 2px; background: var(--gold); }

  .wave { position: absolute; inset: 0; }

  .brand { position: absolute; left: 40px; top: 60px; width: 250px; text-align: center; }
  .brand-dot { width: 120px; height: 120px; border-radius: 50%; background: var(--gold); margin: 0 auto 22px; }
  .brand-name { font-weight: 700; font-size: 24px; color: var(--blue); letter-spacing: 0.5px; white-space: nowrap; }

  .person { position: absolute; right: 30px; top: 30px; text-align: right; }
  .person-name { font-weight: 700; font-size: 24px; color: var(--blue); line-height: 1.1; }
  .person-role { font-size: 16px; margin-top: 4px; }

  .contact-line {
    position: absolute; right: 30px;
    display: flex; align-items: center; gap: 12px; font-size: 16px;
  }
  .contact-line svg { width: 15px; height: 15px; flex: none; }
  .phone { font-weight: 600; font-size: 17px; letter-spacing: 0.5px; }
  .address { position: absolute; right: 29px; top: 252px; text-align: right; font-size: 16px; line-height: 1.4; }
</style>
</head>
<body>

<section class="card card-front">
  <div class="front-name">HARBORLINE AUTO</div>
  <div class="front-web"><span class="rule"></span><span>www.harborlineautoxq.net</span><span class="rule"></span></div>
</section>

<section class="card card-back">
  <svg class="wave" viewBox="0 0 618 374" preserveAspectRatio="none">
    <defs>
      <linearGradient id="blueBand" x1="0" y1="1" x2="1" y2="0">
        <stop offset="0" stop-color="#2a8ccc"/>
        <stop offset="1" stop-color="#15587f"/>
      </linearGradient>
    </defs>
    <path d="M0,300 C140,345 280,330 380,270 C460,222 540,200 618,202 L618,374 L0,374 Z" fill="url(#blueBand)"/>
    <path d="M0,262 C110,305 250,318 380,238 C460,190 540,172 618,178 L618,190 C540,186 470,205 390,252 C260,330 110,318 0,282 Z" fill="var(--gold)"/>
    <path d="M40,285 C150,330 260,320 350,288 C260,335 140,330 40,285 Z" fill="var(--gold)"/>
  </svg>

  <div class="brand">
    <div class="brand-dot"></div>
    <div class="brand-name">HARBORLINE AUTO</div>
  </div>

  <div class="person">
    <div class="person-name">Darren Kellow</div>
    <div class="person-role">Managing Director</div>
  </div>

  <div class="contact-line" style="top:94px">
    <span class="phone">931-555-0148</span>
    <svg viewBox="0 0 16 16"><path d="M3 1h3l1 4-2 1c1 2 3 4 5 5l1-2 4 1v3c0 1-1 2-2 2C7 15 1 9 1 3c0-1 1-2 2-2z" fill="var(--gold)"/></svg>
  </div>
  <div class="contact-line" style="top:116px">
    <span class="phone">629-555-0173</span>
    <svg viewBox="0 0 16 16"><path d="M3 1h3l1 4-2 1c1 2 3 4 5 5l1-2 4 1v3c0 1-1 2-2 2C7 15 1 9 1 3c0-1 1-2 2-2z" fill="var(--gold)"/></svg>
  </div>

  <div class="address">2874 Cresthaven Road,<br>Shelbyville, TN 37162</div>

  <div class="contact-line" style="top:306px">
    <span>www.harborlineautoxq.net</span>
    <svg viewBox="0 0 16 16"><circle cx="8" cy="8" r="6.5" fill="none" stroke="var(--gold)" stroke-width="1.5"/><path d="M1.5 8h13M8 1.5c-3 3-3 10 0 13M8 1.5c3 3 3 10 0 13" fill="none" stroke="var(--gold)" stroke-width="1.2"/></svg>
  </div>
  <div class="contact-line" style="top:328px">
    <span>harborlineautoxq@mailnest.example</span>
    <svg viewBox="0 0 16 16"><rect x="1" y="3" width="14" height="10" rx="1" fill="var(--gold)"/><path d="M1 4l7 5 7-5" fill="none" stroke="#1f1f22" stroke-width="1.2"/></svg>
  </div>
</section>

</body>
</html>
```